Business Card Design

We need a business card designed for our new company. Prefer a black card with white logo & writing.

Contact Information for Business Card

Ted Galloway, address: 7-4812 Fernhollow Road, Abbotsford, BC, V3K 8R2, Office Phone: 604-712-3390, Cell: 604-947-2164, Email: ted@resinworkshub.ca

Colors

Designer to choose only greyscale colors for use in the design.

```html
<!DOCTYPE html>
<html lang="en">
<head>
<meta charset="utf-8">
<title>Resinworks Hub – Business Card</title>
<link href="https://fonts.googleapis.com/css2?family=Poppins:wght@300;400;700&display=swap" rel="stylesheet">
<style>
  :root {
    --backdrop: #1f1f21;
    --card: #1e1e20;
    --card-edge: #2a2a2d;
    --emboss: #0e0e10;
    --ink: #ffffff;
    --ink-soft: #e6e6e6;
    --glyph: #1e1e20;
  }
  * { margin: 0; padding: 0; box-sizing: border-box; }
  html, body {
    width: 1200px; height: 711px; overflow: hidden;
    background: var(--backdrop);
    font-family: "Poppins", sans-serif;
  }
  .stage {
    position: relative; width: 1200px; height: 711px;
    display: flex; justify-content: center; align-items: center; gap: 70px;
  }
  .card {
    width: 320px; height: 560px;
    background: var(--card);
    border: 1px solid var(--card-edge);
    border-radius: 22px;
    box-shadow: 0 14px 30px rgba(0,0,0,.55);
    position: relative;
    color: var(--ink);
  }
  /* Front: embossed brand name */
  .card--front { display: flex; align-items: center; justify-content: center; }
  .brand-emboss {
    transform: rotate(-90deg);
    font-weight: 700; font-size: 40px; letter-spacing: 2px;
    color: var(--emboss); white-space: nowrap; line-height: 1;
  }
  /* Back: contact side */
  .card--back { text-align: center; }
  .brand {
    position: absolute; top: 62px; left: 0; right: 0;
    font-weight: 700; font-size: 27px; letter-spacing: 1px; line-height: 1.1;
    color: var(--ink);
  }
  .person { position: absolute; top: 272px; left: 0; right: 0; }
  .person__name { font-size: 27px; line-height: 1; }
  .person__first { font-weight: 700; }
  .person__last { font-weight: 300; }
  .person__title { font-size: 11.5px; font-weight: 400; margin-top: 4px; color: var(--ink-soft); }

  .divider {
    position: absolute; left: 26px; right: 26px;
    display: flex; align-items: center; gap: 8px;
  }
  .divider__rule { flex: 1; height: 1.5px; background: var(--ink); }
  .divider__icons { display: flex; gap: 5px; }
  .divider--contacts { top: 336px; }
  .divider--address { top: 448px; }

  .hex-icon { width: 22px; height: 22px; display: block; }

  .contacts {
    position: absolute; top: 368px; left: 0; right: 0;
    list-style: none; font-size: 13px; font-weight: 300; line-height: 17px;
    color: var(--ink-soft);
  }
  .address {
    position: absolute; top: 482px; left: 0; right: 0;
    font-style: normal; font-size: 13px; font-weight: 300; line-height: 17px;
    color: var(--ink-soft);
  }
</style>
</head>
<body>
<main class="stage">
  <section class="card card--front" aria-label="Card front">
    <p class="brand-emboss">RESINWORKS HUB</p>
  </section>

  <section class="card card--back" aria-label="Card back">
    <p class="brand">RESINWORKS<br>HUB</p>

    <div class="person">
      <p class="person__name"><span class="person__first">Ted</span> <span class="person__last">Galloway</span></p>
      <p class="person__title">Founder &amp; CEO</p>
    </div>

    <div class="divider divider--contacts">
      <span class="divider__rule"></span>
      <span class="divider__icons">
        <svg class="hex-icon" viewBox="0 0 24 24" aria-label="Phone">
          <polygon points="12,1 22,6.5 22,17.5 12,23 2,17.5 2,6.5" fill="var(--ink)"/>
          <path d="M8.5 7.5l2 0 1 2.5-1.3 1a6 6 0 0 0 2.8 2.8l1-1.3 2.5 1v2a1 1 0 0 1-1 1A8 8 0 0 1 7.5 8.5a1 1 0 0 1 1-1z" fill="var(--glyph)"/>
        </svg>
        <svg class="hex-icon" viewBox="0 0 24 24" aria-label="Office phone">
          <polygon points="12,1 22,6.5 22,17.5 12,23 2,17.5 2,6.5" fill="var(--ink)"/>
          <rect x="7" y="8" width="10" height="8" rx="1" fill="var(--glyph)"/>
          <rect x="9" y="6" width="6" height="3" fill="var(--glyph)"/>
        </svg>
        <svg class="hex-icon" viewBox="0 0 24 24" aria-label="Email">
          <polygon points="12,1 22,6.5 22,17.5 12,23 2,17.5 2,6.5" fill="var(--ink)"/>
          <rect x="6.5" y="8" width="11" height="8" fill="none" stroke="var(--glyph)" stroke-width="1.5"/>
          <path d="M6.5 8l5.5 4.5 5.5-4.5" fill="none" stroke="var(--glyph)" stroke-width="1.5"/>
        </svg>
        <svg class="hex-icon" viewBox="0 0 24 24" aria-label="Website">
          <polygon points="12,1 22,6.5 22,17.5 12,23 2,17.5 2,6.5" fill="var(--ink)"/>
          <circle cx="12" cy="12" r="5.5" fill="none" stroke="var(--glyph)" stroke-width="1.4"/>
          <path d="M6.5 12h11M12 6.5c-2.5 3-2.5 8 0 11M12 6.5c2.5 3 2.5 8 0 11" fill="none" stroke="var(--glyph)" stroke-width="1.1"/>
        </svg>
      </span>
      <span class="divider__rule"></span>
    </div>

    <ul class="contacts">
      <li>604-712-3390</li>
      <li>604-947-2164</li>
      <li>www.resinworkshub.ca</li>
      <li>ted@resinworkshub.ca</li>
    </ul>

    <div class="divider divider--address">
      <span class="divider__rule"></span>
      <svg class="hex-icon" viewBox="0 0 24 24" aria-label="Location">
        <polygon points="12,1 22,6.5 22,17.5 12,23 2,17.5 2,6.5" fill="var(--ink)"/>
        <path d="M12 17.5s-4.5-4.6-4.5-7.5a4.5 4.5 0 0 1 9 0c0 2.9-4.5 7.5-4.5 7.5z" fill="var(--glyph)"/>
        <circle cx="12" cy="10" r="1.6" fill="var(--ink)"/>
      </svg>
      <span class="divider__rule"></span>
    </div>

    <address class="address">
      7-4812 Fernhollow Road,<br>
      Abbotsford, BC, V3K 8R2.
    </address>
  </section>
</main>
</body>
</html>
```